Stationery Design Project

Fire and building compliance company needs business card, letterhead and complement slip designed.
Have included a brief about business card, basic want front keep quite clean with just the KTV logo and the words Marlowby Alarm and Guard 2012 Ltd (small print) along the bottom. Website needs to be included (www.ktvalarm.example.nz) on either front or back.
The info for back is as per attachment.
Letterhead and complement slip should have the usual stuff KTV logo etc and also the accredited test lab logo at the bottom (can be small size)
Target Market(s)
Property owners, buisness managers
Industry/Entity Type
Building
Look and feel
Each slider illustrates characteristics of the customer's brand and the style your logo design should communicate.

```html
<!DOCTYPE html>
<html lang="en">
<head>
<meta charset="utf-8">
<title>KTV Business Card</title>
<link href="https://fonts.googleapis.com/css2?family=Open+Sans:wght@400;600;700&display=swap" rel="stylesheet">
<style>
  :root {
    --bg: #e9e6e1;
    --card-dark: #2b2c2e;
    --card-dark-edge: #1c1d1f;
    --card-light: #ffffff;
    --ink: #4a4b4d;
    --ink-soft: #8a8b8d;
    --orange: #f07522;
    --blue: #1e6f9c;
    --navy: #1d2a6b;
    --rule: #c9c9c9;
    --band: #3a3b3d;
  }
  * { box-sizing: border-box; margin: 0; padding: 0; }
  html, body { width: 1200px; height: 900px; overflow: hidden; }
  body {
    background: var(--bg);
    font-family: "Open Sans", Arial, sans-serif;
    position: relative;
  }
  .card {
    position: absolute;
    left: 300px;
    width: 600px;
    height: 365px;
    border-radius: 3px;
    box-shadow: 0 6px 18px rgba(0,0,0,.18);
    overflow: hidden;
  }
  /* Back of card */
  .card-back {
    top: 55px;
    background: linear-gradient(160deg, #343537 0%, var(--card-dark) 55%, var(--card-dark-edge) 100%);
    color: #fff;
    text-align: center;
  }
  .brand {
    display: flex;
    align-items: center;
    gap: 10px;
  }
  .brand-dot {
    width: 34px; height: 34px;
    border-radius: 50%;
    background: var(--orange);
    flex: none;
  }
  .brand-name {
    font-weight: 700;
    font-size: 40px;
    line-height: 1;
    letter-spacing: 1px;
  }
  .brand-tagline {
    font-size: 12px;
    line-height: 1.05;
    color: var(--ink-soft);
  }
  .card-back .brand {
    justify-content: center;
    margin-top: 58px;
  }
  .card-back .brand-name { color: #f2f2f2; }
  .card-back .brand-tagline { color: #b5b5b5; text-align: left; }
  .services-title {
    margin-top: 22px;
    font-weight: 700;
    font-size: 15px;
  }
  .services {
    list-style: none;
    margin-top: 4px;
    font-size: 13.5px;
    line-height: 1.45;
  }
  .services li::before {
    content: "";
    display: inline-block;
    width: 6px; height: 6px;
    border: 1px solid #fff;
    border-radius: 50%;
    margin-right: 8px;
    vertical-align: 2px;
  }
  /* Front of card */
  .card-front {
    top: 470px;
    background: var(--card-light);
    color: var(--ink);
  }
  .card-front .brand {
    position: absolute;
    left: 40px;
    top: 40px;
  }
  .card-front .brand-dot { width: 44px; height: 44px; }
  .card-front .brand-name { font-size: 50px; color: var(--ink); }
  .header-rule {
    position: absolute;
    left: 40px; right: 40px; top: 128px;
    height: 1px;
    background: var(--rule);
  }
  .company {
    position: absolute;
    left: 40px; top: 140px;
    font-size: 13px;
    line-height: 1.35;
  }
  .contacts {
    position: absolute;
    left: 40px; top: 186px;
    display: grid;
    grid-template-columns: 90px auto;
    column-gap: 14px;
    row-gap: 4px;
    font-size: 13px;
  }
  .contact { display: flex; align-items: center; gap: 6px; white-space: nowrap; }
  .contact svg { width: 13px; height: 13px; flex: none; }
  .accreditation {
    position: absolute;
    right: 40px; top: 190px;
    width: 54px; height: 44px;
    border-radius: 4px;
    background: var(--navy);
  }
  .person {
    position: absolute;
    right: 40px; top: 246px;
    text-align: right;
  }
  .person-name {
    color: var(--orange);
    font-weight: 700;
    font-size: 15px;
    padding-bottom: 2px;
    border-bottom: 1px solid var(--rule);
    padding-left: 60px;
  }
  .person-role { font-size: 13px; margin-top: 2px; }
  .footer-line {
    position: absolute;
    left: 0; right: 0; bottom: 22px;
    height: 2px;
    background: var(--orange);
  }
  .footer-band {
    position: absolute;
    left: 0; right: 0; bottom: 0;
    height: 16px;
    background: linear-gradient(180deg, #4a4b4d, var(--band));
  }
</style>
</head>
<body>

<section class="card card-back">
  <div class="brand">
    <span class="brand-dot"></span>
    <div>
      <div class="brand-name">KTV</div>
      <div class="brand-tagline">Fire and Building<br>Compliance</div>
    </div>
  </div>
  <h2 class="services-title">Our services</h2>
  <ul class="services">
    <li>Building compliance specialists</li>
    <li>Building warrant of fitness preparation</li>
    <li>Fire alarms, Fire Extinguishers &amp;emergency lighting</li>
    <li>Approved evacuation schemes</li>
    <li>Pressure testing LPG CNG Fire extinguishers</li>
    <li>Security alarm and CCTV systems</li>
  </ul>
</section>

<section class="card card-front">
  <div class="brand">
    <span class="brand-dot"></span>
    <div>
      <div class="brand-name">KTV</div>
      <div class="brand-tagline">Fire and Building<br>Compliance</div>
    </div>
  </div>
  <div class="header-rule"></div>

  <address class="company" style="font-style:normal">
    Marlowby Alarm and Guard<br>
    14 Harlow Lane Extension, Eastvale, 4599
  </address>

  <div class="contacts">
    <div class="contact">
      <svg viewBox="0 0 16 16" aria-hidden="true"><circle cx="8" cy="8" r="8" fill="#f07522"/><path d="M5 4.5c.5-.5 1-.5 1.3 0l.8 1.3c.2.4 0 .8-.3 1l-.5.4c.4 1 1.2 1.8 2.2 2.2l.4-.5c.3-.3.7-.4 1-.2l1.3.8c.5.3.5.8 0 1.3-.8.8-2 .9-3.2.2C6.3 10.2 5 8.8 4.6 7.6 4.2 6.4 4.3 5.2 5 4.5z" fill="#fff"/></svg>
      06 555 0182
    </div>
    <div class="contact">
      <svg viewBox="0 0 16 16" aria-hidden="true"><circle cx="8" cy="8" r="8" fill="#f07522"/><text x="8" y="11.5" font-size="10" font-weight="700" text-anchor="middle" fill="#fff" font-family="Open Sans, sans-serif">@</text></svg>
      admin@marlowby.example.nz
    </div>
    <div class="contact">
      <svg viewBox="0 0 16 16" aria-hidden="true"><circle cx="8" cy="8" r="8" fill="#f07522"/><rect x="5" y="3.5" width="6" height="3" fill="#fff"/><rect x="3.5" y="6.5" width="9" height="4" rx="1" fill="#fff"/><rect x="5" y="9.5" width="6" height="3" fill="#fff" stroke="#f07522" stroke-width=".6"/></svg>
      06 555 0147
    </div>
    <div class="contact">
      <svg viewBox="0 0 16 16" aria-hidden="true"><circle cx="8" cy="8" r="8" fill="#f07522"/><circle cx="8" cy="8" r="4.2" fill="none" stroke="#fff" stroke-width="1"/><path d="M3.8 8h8.4M8 3.8c-1.6 2.4-1.6 6 0 8.4M8 3.8c1.6 2.4 1.6 6 0 8.4" fill="none" stroke="#fff" stroke-width=".8"/></svg>
      www.ktvalarm.example.nz
    </div>
  </div>

  <div class="accreditation" role="img" aria-label="Accredited laboratory badge"></div>

  <div class="person">
    <div class="person-name">Dana Whitcombe</div>
    <div class="person-role">Director</div>
  </div>

  <div class="footer-line"></div>
  <div class="footer-band"></div>
</section>

</body>
</html>
```